Vantiqo custom business card design

Need a authentic, innovative business card design for a new mobile app business. I am uploading a few screen images from our app for you to view. I would like app design theme to match business card design. I can also send logo images.

```html
<!DOCTYPE html>
<html lang="en">
<head>
<meta charset="UTF-8">
<title>Vantiqo Business Card</title>
<link href="https://fonts.googleapis.com/css2?family=Work+Sans:wght@400;500;700&display=swap" rel="stylesheet">
<style>
  :root {
    --page-bg: #161616;
    --card-bg: #262626;
    --card-edge: #303030;
    --text-light: #f2f2f2;
    --accent-purple: #6b2fa8;
    --logo-silver: #d8d8d8;
  }
  * { margin: 0; padding: 0; box-sizing: border-box; }
  html, body {
    width: 1200px;
    height: 900px;
    overflow: hidden;
    background: var(--page-bg);
    font-family: "Work Sans", sans-serif;
  }
  .stage {
    width: 1200px;
    height: 900px;
    display: flex;
    flex-direction: column;
    align-items: center;
    justify-content: center;
    gap: 40px;
  }
  .card {
    width: 600px;
    height: 343px;
    background: var(--card-bg);
    border: 1px solid var(--card-edge);
    position: relative;
  }
  .card-front {
    display: flex;
    flex-direction: column;
    align-items: center;
    justify-content: center;
    gap: 18px;
  }
  .brand-dot {
    width: 110px;
    height: 110px;
    border-radius: 50%;
    background: var(--logo-silver);
  }
  .brand-name {
    font-size: 40px;
    font-weight: 700;
    color: var(--logo-silver);
    letter-spacing: 0.5px;
  }
  .card-back {
    display: flex;
    align-items: center;
    justify-content: center;
  }
  .identity {
    text-align: right;
    padding-right: 26px;
    color: var(--text-light);
  }
  .person-name {
    font-size: 25px;
    font-weight: 500;
    color: var(--accent-purple);
    letter-spacing: 1px;
    text-transform: uppercase;
    margin-bottom: 2px;
  }
  .person-role, .address-line {
    font-size: 18px;
    line-height: 1.4;
    letter-spacing: 0.6px;
  }
  .person-role { margin-bottom: 2px; }
  .divider {
    width: 2px;
    height: 112px;
    background: var(--accent-purple);
  }
  .contacts {
    list-style: none;
    padding-left: 24px;
    color: var(--text-light);
  }
  .contact-item {
    display: flex;
    align-items: center;
    gap: 12px;
    font-size: 18px;
    line-height: 1.45;
    letter-spacing: 0.6px;
  }
  .contact-icon {
    width: 14px;
    height: 14px;
    flex: none;
  }
</style>
</head>
<body>
  <main class="stage">
    <section class="card card-front">
      <div class="brand-dot"></div>
      <div class="brand-name">Vantiqo</div>
    </section>

    <section class="card card-back">
      <div class="identity">
        <p class="person-name">Daniel Reyes</p>
        <p class="person-role">Director</p>
        <p class="address-line">1428 Harbor Lane</p>
        <p class="address-line">Coral Bay, FL 32190</p>
      </div>
      <div class="divider"></div>
      <ul class="contacts">
        <li class="contact-item">
          <svg class="contact-icon" viewBox="0 0 14 14"><rect x="3.5" y="1" width="7" height="12" rx="1.2" fill="none" stroke="#6b2fa8" stroke-width="1.4"/><line x1="6" y1="11" x2="8" y2="11" stroke="#6b2fa8" stroke-width="1.2"/></svg>
          <span>(253) 555-0142</span>
        </li>
        <li class="contact-item">
          <svg class="contact-icon" viewBox="0 0 14 14"><path d="M3 1.5 L5.5 1.5 L6.2 4.5 L4.6 5.6 C5.4 7.4 6.6 8.6 8.4 9.4 L9.5 7.8 L12.5 8.5 L12.5 11 C12.5 11.8 11.8 12.5 11 12.5 C6 12.2 1.8 8 1.5 3 C1.5 2.2 2.2 1.5 3 1.5 Z" fill="#6b2fa8"/></svg>
          <span>(253) 555-0187</span>
        </li>
        <li class="contact-item">
          <svg class="contact-icon" viewBox="0 0 14 14"><rect x="1" y="3" width="12" height="8.5" fill="none" stroke="#6b2fa8" stroke-width="1.3"/><polyline points="1,3 7,8 13,3" fill="none" stroke="#6b2fa8" stroke-width="1.3"/></svg>
          <span>info@vantiqo.com</span>
        </li>
        <li class="contact-item">
          <svg class="contact-icon" viewBox="0 0 14 14"><circle cx="7" cy="7" r="5.8" fill="none" stroke="#6b2fa8" stroke-width="1.2"/><ellipse cx="7" cy="7" rx="2.5" ry="5.8" fill="none" stroke="#6b2fa8" stroke-width="1.1"/><line x1="1.2" y1="7" x2="12.8" y2="7" stroke="#6b2fa8" stroke-width="1.1"/></svg>
          <span>www.vantiqo.com</span>
        </li>
      </ul>
    </section>
  </main>
</body>
</html>
```